3D abstract logo Construction, Kitchen and Bath design and Project Management Business Card Design

I want a 3d abstract logo for a new General Construction, Kitchen and Bath design and Project Management Company located at Philadelphia PA, we want to put our logo in the white color trucks too. I want to look professional and serious at the same time look like an architect design and the warm originals color that make you feel in a nice decorated home, I like the colors trend in this link:
http://www.quellmark.example/qm/ggs/pageeditor.aspx?alt_doc_id=RT41K-M9B33-2W5&doc_id=5913046628&pf_id=D4H

I was thinking about a roof and the PA font could have square shape or like wood framing with two tones of the brick color black and creamy yellow color.... Also I like the keystone Idea like the modification or the Ridgeline Parkway logo but curvy at the top

The final design should communicate big company (because we want to grow), responsible, professional and organized that really care about our customers and give them everything they need... plan and design, excellent labor and Project Management
Updates

I doesn't have to be 3d

Reason: I haven't received enough options...

Please stick with the warm tones shown in the image001 attached I like spicy cinnamon instead a cold wine or brick color and also the cream yellowish tones added

Hello designers, please use only the idea and colors of the image001 I don't want to be stick with a house logo because I do commercial construction too so I prefer work around the keystone idea maybe leaving the style of the PA.
I'd like the base tone on the card dark like first option and you can send me a white option too.

Please send me your ideas as soon as possible 

Thank you so much!

Target Market(s)

Builders, State, commercial business owners, Property owners or Real State and Property Management Companies

Industry/Entity Type

Architect

Contact Information for Business Card

RK Buildworks LLC
“Your project is our business”
Lorna Vasquel Eng.
President
Commercial & Residential General Construction
Kitchen & Bath Design | Project Management
Phone: 555-304-7718 | Fax: 555-304-7719 Cell: 555-862-3097
lorna@rkbuildworks.example

```html
<!DOCTYPE html>
<html lang="en">
<head>
<meta charset="utf-8">
<title>RK Buildworks – Business Card Set</title>
<link rel="stylesheet" href="https://fonts.googleapis.com/css2?family=Arimo:ital,wght@0,400;0,700;1,400&family=Varela+Round&display=swap">
<style>
  :root {
    --cinnamon: #7a2320;
    --rose: #b0665f;
    --cocoa: #8c5f48;
    --cream: #f3ecdc;
    --sand: #e2c083;
    --ink: #2e2a26;
    --paper: #ffffff;
  }
  * { margin: 0; padding: 0; box-sizing: border-box; }
  html, body { width: 741px; height: 1200px; overflow: hidden; background: var(--paper); }
  body { position: relative; font-family: "Arimo", Arial, sans-serif; color: var(--cream); }

  .card-front { position: absolute; left: 0; top: 0; width: 741px; height: 435px; background: var(--cinnamon); overflow: hidden; }
  .accent-band { position: absolute; left: 612px; top: 0; width: 129px; height: 435px; background: linear-gradient(180deg, var(--cream) 0%, var(--cream) 55%, var(--sand) 100%); }
  .holder-name { position: absolute; left: 37px; top: 36px; font-size: 40px; font-weight: 700; letter-spacing: 0.3px; }
  .holder-title { position: absolute; left: 38px; top: 85px; font-size: 24px; font-style: italic; }
  .services { position: absolute; left: 37px; top: 142px; font-family: "Varela Round", Verdana, sans-serif; font-size: 23.5px; letter-spacing: 0.9px; line-height: 28px; white-space: nowrap; }
  .contacts { position: absolute; left: 37px; top: 283px; font-size: 18px; line-height: 32.5px; }
  .contacts .row { display: flex; }
  .contacts .label { width: 103px; }
  .brand-seal { position: absolute; left: 540px; top: 243px; width: 150px; height: 150px; border-radius: 50%; background: var(--cinnamon); display: flex; align-items: center; justify-content: center; }
  .brand-name { font-family: "Arimo", Arial, sans-serif; font-weight: 700; font-size: 15px; color: var(--cream); letter-spacing: 0.5px; white-space: nowrap; }

  .card-back { position: absolute; left: 5px; top: 458px; width: 433px; height: 740px; background: var(--cinnamon); text-align: center; }
  .card-back .brand-dot { position: absolute; left: 156px; top: 250px; width: 120px; height: 120px; border-radius: 50%; background: var(--cream); }
  .card-back .brand-name { position: absolute; left: 0; right: 0; top: 445px; font-size: 21px; font-weight: 400; }
  .tagline { position: absolute; left: 0; right: 0; top: 484px; font-size: 24px; }
  .website { position: absolute; left: 0; right: 0; top: 637px; font-size: 17px; }

  .swatch { position: absolute; }
  .swatch.cinnamon { left: 467px; top: 473px; width: 121px; height: 72px; background: var(--cinnamon); }
  .swatch.rose { left: 467px; top: 545px; width: 121px; height: 70px; background: var(--rose); }
  .swatch.cocoa { left: 594px; top: 473px; width: 123px; height: 72px; background: var(--cocoa); }
  .swatch.cream { left: 594px; top: 545px; width: 123px; height: 82px; background: var(--cream); }
  .swatch.sand { left: 597px; top: 627px; width: 118px; height: 71px; background: var(--sand); }

  .card-alt { position: absolute; left: 466px; top: 711px; width: 250px; height: 487px; background: var(--cinnamon); overflow: hidden; }
  .info-plate { position: absolute; left: 24px; top: 2px; width: 228px; height: 272px; border-radius: 5px; background: linear-gradient(90deg, var(--sand) 0%, #c69a6c 55%, var(--cocoa) 100%); }
  .info-text { position: absolute; left: 40px; top: 262px; transform: rotate(-90deg); transform-origin: 0 0; color: var(--ink); font-size: 24px; line-height: 35px; white-space: nowrap; }
  .brand-square { position: absolute; left: 31px; top: 301px; width: 140px; height: 148px; border-radius: 4px; background: var(--rose); }
  .card-alt .brand-name { position: absolute; left: 182px; top: 455px; transform: rotate(-90deg); transform-origin: 0 0; font-size: 27px; font-weight: 400; letter-spacing: 0; }
</style>
</head>
<body>

<section class="card-front">
  <div class="accent-band" role="img" aria-label="Decorative curved stripe band in cream, sand, rose and cocoa"></div>
  <h1 class="holder-name">LORNA VASQUEL</h1>
  <p class="holder-title">Eng. President</p>
  <p class="services">Commercial &amp; Residential General<br>Construction Kitchen &amp; Bath Design</p>
  <div class="contacts">
    <div class="row"><span class="label">Phone:</span><span>555-304-7718</span></div>
    <div class="row"><span class="label">Fax:</span><span>555-304-7719</span></div>
    <div class="row"><span class="label">Cell:</span><span>555-862-3097</span></div>
    <div class="row"><span class="label">Email:</span><span>lorna@rkbuildworks.example</span></div>
  </div>
  <div class="brand-seal"><span class="brand-name">RK BUILDWORKS</span></div>
</section>

<section class="card-back">
  <div class="brand-dot"></div>
  <p class="brand-name">RK BUILDWORKS</p>
  <p class="tagline">Your project is our business</p>
  <p class="website">www.rkbuildworks.example</p>
</section>

<div class="palette">
  <div class="swatch cinnamon"></div>
  <div class="swatch rose"></div>
  <div class="swatch cocoa"></div>
  <div class="swatch cream"></div>
  <div class="swatch sand"></div>
</div>

<section class="card-alt">
  <div class="info-plate"></div>
  <div class="info-text">Lorna Vasquel<br>(555) 555-0142<br>RKbuildworks.example<br>Email: ....</div>
  <div class="brand-square"></div>
  <span class="brand-name">RK Buildworks</span>
</section>

</body>
</html>
```